TorbCutters Website & website development in Wordpress

Simple website for a 5 pages with some 15 products for sale.
We will sell T shirts and other Viking mens grooming products.

*****Lady barbers****
Also the company that gets awarded this job needs to be able to give me a quote to build the site in wordpress, just a design will not work.

Target Market(s)

The adventurous person likes to travels and get a good haircut

Coding

Coded - Design and coding required

Number of Pages Required

5+ page

Font styles to use
Sans Serif

Colors
3176b5
33a6d7

Requirements
Must have
• Must have a product order page for T-Shirts
Must have a travel adventure page with up to 5 recommended adventures
Must have a link to our instagram @torbcuttersformen page that would allow a client to book a haircut
Should show female stylists cutting mens hair- So far the only pictures in the designs submitted are male barbers
Nice to have
• We have this set up in GoDaddy would like to use wordpress. Thanks!

```html
<!DOCTYPE html>
<html lang="en">
<head>
<meta charset="utf-8">
<title>TorbCutters – Haircuts for Men</title>
<link rel="stylesheet" href="https://fonts.googleapis.com/css2?family=Oswald:wght@400;500;600&family=Montserrat:wght@400;500;600&display=swap">
<style>
:root{
  --blue:#3176b5;
  --sky:#33a6d7;
  --red:#d41a2b;
  --ink:#1d1d1f;
  --text:#3c3c3c;
  --pale:#dcedf6;
  --line:#e6e6e6;
  --dark:#202325;
  --white:#ffffff;
}
*{margin:0;padding:0;box-sizing:border-box}
html,body{width:1200px;height:5348px;overflow:hidden}
body{position:relative;background:var(--white);font-family:"Montserrat",Arial,sans-serif;color:var(--text)}
.abs{position:absolute}
.heading{font-family:"Oswald",Arial,sans-serif;font-weight:500;color:var(--ink);text-transform:uppercase;text-align:center;letter-spacing:1px}
.section-title{position:absolute;left:0;width:1200px;font-size:48px;line-height:1}
.title-rule{position:absolute;left:585px;width:30px;height:3px;background:var(--blue)}
.btn{position:absolute;display:flex;align-items:center;justify-content:center;font-family:"Oswald",Arial,sans-serif;font-weight:500;font-size:13px;letter-spacing:.5px;color:var(--white);text-transform:uppercase;background:var(--blue)}
.btn.red{background:var(--red)}
.centered{position:absolute;left:0;width:1200px;text-align:center}

/* hero */
.hero{position:absolute;left:0;top:0;width:1200px;height:560px;
  background:
    radial-gradient(ellipse 30% 55% at 88% 35%,#6b5a4a 0%,#4a3f36 45%,transparent 75%),
    radial-gradient(ellipse 40% 40% at 20% 70%,#5f6668 0%,transparent 70%),
    linear-gradient(180deg,#3e4446 0%,#5a6062 40%,#3a3e40 75%,#2a2d2f 100%)}
.hero-phone{position:absolute;left:162px;top:40px;display:flex;align-items:center;gap:8px;color:var(--white);font-family:"Oswald",sans-serif;font-size:16px}
.hero-phone .ico{width:30px;height:30px;background:var(--red);display:flex;align-items:center;justify-content:center}
.menu-btn{position:absolute;left:1005px;top:40px;width:30px;height:30px;background:var(--sky);display:flex;flex-direction:column;justify-content:center;align-items:center;gap:4px}
.menu-btn span{width:16px;height:2px;background:var(--white)}
.brand{position:absolute;left:0;top:150px;width:1200px;display:flex;justify-content:center;align-items:center;gap:24px}
.brand-name{font-family:"Oswald",sans-serif;font-weight:600;font-size:150px;line-height:1;color:var(--white);letter-spacing:2px}
.brand-mark{width:120px;height:120px;border-radius:50%;background:var(--red)}
.brand-tag{position:absolute;left:0;top:372px;width:1200px;text-align:center;font-family:"Oswald",sans-serif;font-size:34px;letter-spacing:12px;color:var(--white)}

/* about */
.about-sub{position:absolute;left:0;top:702px;width:1200px;text-align:center;font-family:"Oswald",sans-serif;font-size:22px;color:var(--blue);letter-spacing:1px}
.about-lead{top:775px;font-size:13px;line-height:22px;color:var(--red)}
.about-body{top:830px;left:160px;width:880px;font-size:13px;line-height:25px;color:var(--text)}

/* features */
.photo{position:absolute}
.feature{position:absolute;width:400px}
.feature .fico{width:46px;height:46px;border-radius:50%;background:var(--blue);margin-bottom:18px}
.feature h4{font-family:"Oswald",sans-serif;font-weight:500;font-size:15px;color:var(--ink);margin-bottom:8px}
.feature p{font-size:13px;line-height:26px}

/* appointment */
.band{position:absolute;left:0;width:1200px;background:var(--pale)}
.appt-text{top:1786px;left:240px;width:720px;font-size:16px;line-height:29px;color:var(--ink)}
.field{position:absolute;top:1870px;width:208px;height:40px;background:var(--white);border:1px solid #cfd7dc;display:flex;align-items:center;padding-left:14px;gap:10px;font-size:12px;color:#9a9a9a}

/* services */
.svc-text{top:2164px;font-size:16px;line-height:29px;color:var(--ink)}
.svc-card{position:absolute;top:2259px;width:204px;height:319px;background:var(--white);border:1px solid var(--line);text-align:center;padding-top:50px}
.svc-card.active{background:#262a2d;border-color:#262a2d}
.svc-card .icon-wrap{position:relative;width:130px;height:70px;margin:0 auto}
.svc-card .backdrop{position:absolute;left:20px;top:-20px;width:90px;height:90px;border-radius:50%;background:#f1f1f1}
.svc-card.active .backdrop{background:#33383b}
.svc-card .icon-wrap svg{position:relative;margin-top:4px}
.svc-card h5{font-family:"Oswald",sans-serif;font-weight:500;font-size:15px;color:var(--ink);margin-top:2px}
.svc-card p{font-size:12px;line-height:21px;margin:10px auto 0;width:160px}
.svc-card .more{font-family:"Oswald",sans-serif;font-size:13px;color:var(--ink);margin-top:22px}
.svc-card.active h5,.svc-card.active .more,.svc-card.active p{color:var(--white)}
.arrow-box{position:absolute;width:32px;height:32px;border:1px solid #b9c9d6;display:flex;align-items:center;justify-content:center;background:var(--white)}

/* reviews */
.quote-mark{position:absolute;left:160px;top:2800px;font-family:"Oswald",sans-serif;font-size:120px;line-height:1;color:#c9dbe6}
.review-text{left:172px;top:2880px;width:370px;font-size:14px;line-height:29px;color:var(--ink)}
.review-name{position:absolute;left:176px;top:3040px;font-family:"Oswald",sans-serif;font-size:17px;color:var(--red)}

/* stylists */
.stylist{position:absolute;top:3398px;width:272px;height:457px}
.stylist .shot{position:absolute;left:0;top:0;width:272px;height:457px;
  background:
    radial-gradient(ellipse 32% 24% at 50% 22%,#d3a587 0%,#a87055 55%,rgba(120,70,45,0) 100%),
    linear-gradient(180deg,rgba(255,255,255,0) 0,rgba(255,255,255,0) 100px,#5a4d44 100px,#3a322d 50%,#1e1b1a 100%)}
.stylist .info{position:absolute;left:0;top:362px;width:272px;text-align:center;color:var(--white)}
.stylist h6{font-family:"Oswald",sans-serif;font-weight:500;font-size:19px;letter-spacing:.5px}
.stylist .role{font-size:13px;margin-top:2px}
.socials{display:flex;justify-content:center;gap:8px;margin-top:8px}
.socials span{width:10px;height:10px;border-radius:50%;background:var(--white)}

/* products */
.product{position:absolute;top:4121px;width:164px;height:276px;border:1px solid var(--line);background:var(--white);text-align:center}
.product .pic{width:110px;height:150px;margin:30px auto 0}
.product h6{font-family:"Oswald",sans-serif;font-weight:500;font-size:15px;color:var(--ink);margin-top:22px}
.product .price{font-size:13px;color:var(--red);margin-top:6px}

/* map & contact */
.map{position:absolute;left:0;top:4559px;width:1200px;height:351px;
  background:
    radial-gradient(ellipse 20% 30% at 20% 40%,#e3ecdf 0%,transparent 70%),
    radial-gradient(ellipse 18% 25% at 85% 70%,#e6eee2 0%,transparent 70%),
    linear-gradient(135deg,#f1f2ef,#e8ebee 60%,#eff0ed)}
.contact{position:absolute;left:0;top:4910px;width:1200px;height:380px;
  background:
    radial-gradient(ellipse 40% 50% at 50% 20%,#3d3a36 0%,transparent 75%),
    linear-gradient(180deg,#2d2b29,#1a1a1a)}
.invite{top:5000px;font-family:"Oswald",sans-serif;font-size:19px;letter-spacing:2px;color:var(--white)}
.invite-phone{top:5028px;font-family:"Oswald",sans-serif;font-size:25px;color:var(--white)}
.info-col{position:absolute;top:5125px;color:var(--white)}
.info-col h6{font-family:"Oswald",sans-serif;font-weight:500;font-size:18px;letter-spacing:1px;display:flex;align-items:center;gap:8px;margin-left:-26px}
.info-col p{font-size:13px;line-height:23px;margin-top:4px;color:#e5e5e5}
.footer{position:absolute;left:0;top:5290px;width:1200px;height:58px;background:var(--blue);color:var(--white);font-size:12px}
.footer .copy{position:absolute;left:162px;top:21px}
.footer .soc{position:absolute;right:162px;top:16px;display:flex;gap:8px}
.footer .soc span{width:26px;height:26px}
</style>
</head>
<body>

<!-- hero -->
<header class="hero" role="img" aria-label="Climber scaling a steep rock face above a misty valley"></header>
<svg class="abs" style="left:0;top:530px" width="1200" height="60" viewBox="0 0 1200 60" aria-hidden="true">
  <polygon points="0,0 1200,0 1200,6 600,40 0,6" fill="#2d3032"/>
  <polygon points="0,6 600,40 1200,6 1200,14 600,48 0,14" fill="var(--red)"/>
  <polygon points="0,14 600,48 1200,14 1200,60 0,60" fill="var(--white)"/>
</svg>
<div class="hero-phone">
  <span class="ico"><svg width="14" height="14" viewBox="0 0 24 24"><path d="M6.6 10.8a15 15 0 0 0 6.6 6.6l2.2-2.2a1 1 0 0 1 1-.25 11 11 0 0 0 3.6.6 1 1 0 0 1 1 1V20a1 1 0 0 1-1 1A17 17 0 0 1 3 4a1 1 0 0 1 1-1h3.5a1 1 0 0 1 1 1 11 11 0 0 0 .6 3.6 1 1 0 0 1-.25 1z" fill="#fff"/></svg></span>
  +1 555 201 4488
</div>
<div class="btn red" style="left:814px;top:40px;width:176px;height:30px">Make an appointment</div>
<div class="menu-btn"><span></span><span></span><span></span></div>
<div class="brand"><span class="brand-name">TORB</span><span class="brand-mark"></span></div>
<div class="brand-tag">HAIRCUTS FOR MEN</div>

<!-- about -->
<h2 class="heading section-title" style="top:652px;font-size:46px">About TorbCutters</h2>
<div class="about-sub">HAIRCUTS FOR MEN</div>
<p class="centered about-lead">Lorem ipsum dolor sit amet, consectetuer adipiscing elit, sed diam nonummy nibh euismod<br>tincidunt ut laoreet dolore magna</p>
<p class="abs about-body" style="text-align:center">Lorem ipsum dolor sit amet, consectetuer adipiscing elit, sed diam nonummy nibh euismod tincidunt ut laoreet dolore magna aliquam erat volutpat. Ut wisi enim ad minim veniam, quis nostrud exerci tation ulla mcorper suscipit lobortis nisl ut aliquip ex ea com modo consequat. Duis autem vel eum iriure dolor in hendrerit in vulputate velit esse molestie consequat, vel illum veniam, quis nostrud exercitation dolore eu feugiat nulla facilisis at</p>
<div class="btn" style="left:542px;top:959px;width:116px;height:38px">Read more</div>

<!-- features -->
<div class="photo" style="left:162px;top:1075px;width:438px;height:237px;background:radial-gradient(ellipse 30% 40% at 60% 45%,#4b4f52 0%,transparent 70%),linear-gradient(160deg,#aab2b8 0%,#dfe4e8 40%,#f4f6f7 70%,#c5ccd1 100%)" role="img" aria-label="Mountaineer climbing a snowy ridge"></div>
<div class="feature" style="left:654px;top:1110px">
  <div class="fico"></div>
  <h4>LOREM IPSUM DOLOR SIT AMET</h4>
  <p>Lorem ipsum dolor sit amet, consectetuer adip<br>iscing elit, sed diam nonummy nibh euismod</p>
</div>
<div class="feature" style="left:162px;top:1348px">
  <div class="fico"></div>
  <h4>LOREM IPSUM DOLOR SIT AMET</h4>
  <p>Lorem ipsum dolor sit amet, consectetuer adip<br>iscing elit, sed diam nonummy nibh euismod</p>
</div>
<div class="photo" style="left:600px;top:1312px;width:440px;height:235px;background:radial-gradient(ellipse 12% 18% at 62% 62%,#c7d83a 0%,transparent 80%),linear-gradient(180deg,#b7cbd9 0%,#8aa6b8 38%,#3d6a7c 58%,#2c5665 72%,#cfdfe2 88%,#9fb8bd 100%)" role="img" aria-label="Surfer riding a wave on a bright board"></div>

<!-- appointment -->
<section class="band" style="top:1621px;height:368px"></section>
<h2 class="heading section-title" style="top:1702px">Make an appointment</h2>
<div class="title-rule" style="top:1764px"></div>
<p class="abs appt-text" style="text-align:center">Lorem ipsum dolor sit amet, consectetuer adipiscing elit, sed diam nonummy nibh euismod tincidunt ut laoreet dolore magna aliquam erat volutpat.</p>
<div class="field" style="left:162px"><svg width="14" height="14" viewBox="0 0 24 24"><circle cx="12" cy="8" r="4" fill="none" stroke="var(--red)" stroke-width="2"/><path d="M4 21a8 8 0 0 1 16 0" fill="none" stroke="var(--red)" stroke-width="2"/></svg>Name</div>
<div class="field" style="left:384px"><svg width="14" height="14" viewBox="0 0 24 24"><path d="M6.6 10.8a15 15 0 0 0 6.6 6.6l2.2-2.2 4.6 1.6V20A17 17 0 0 1 3 4h4l1.6 4.6z" fill="none" stroke="var(--red)" stroke-width="2"/></svg>Phone</div>
<div class="field" style="left:606px"><svg width="14" height="14" viewBox="0 0 24 24"><path d="M3 11l18-8-6 18-3-7z" fill="none" stroke="var(--red)" stroke-width="2"/></svg>Email</div>
<div class="btn" style="left:828px;top:1870px;width:210px;height:40px">Make an appointment</div>

<!-- services -->
<h2 class="heading section-title" style="top:2072px">Our services</h2>
<div class="title-rule" style="top:2134px"></div>
<p class="centered svc-text">TORB Cutters For Men is an amazing barbershop.<br>located in the heart of 48 Harbor Lane, Suite 2 Brookfield, Vermont</p>
<div class="arrow-box" style="left:106px;top:2402px"><svg width="10" height="14" viewBox="0 0 10 14"><path d="M8 1L2 7l6 6" fill="none" stroke="var(--blue)" stroke-width="2"/></svg></div>
<div class="arrow-box" style="left:1061px;top:2402px"><svg width="10" height="14" viewBox="0 0 10 14"><path d="M2 1l6 6-6 6" fill="none" stroke="var(--blue)" stroke-width="2"/></svg></div>

<div class="svc-card" style="left:162px">
  <div class="icon-wrap"><span class="backdrop"></span>
  <svg width="50" height="56" viewBox="0 0 50 56"><circle cx="15" cy="44" r="7" fill="none" stroke="var(--red)" stroke-width="2.5"/><circle cx="35" cy="44" r="7" fill="none" stroke="var(--red)" stroke-width="2.5"/><path d="M19 38L38 4M31 38L12 4" stroke="var(--red)" stroke-width="2.5"/></svg></div>
  <h5>HAIRCUTTING</h5>
  <p>Lorem ipsum dolor sit amet consectetuerad</p>
  <div class="more">READ MORE</div>
</div>
<div class="svc-card active" style="left:386px">
  <div class="icon-wrap"><span class="backdrop"></span>
  <svg width="50" height="56" viewBox="0 0 50 56"><path d="M8 46h34M14 46l6-22h10l6 22" fill="none" stroke="var(--sky)" stroke-width="2.5"/><path d="M22 24l8-18" stroke="var(--sky)" stroke-width="2.5"/></svg></div>
  <h5>SHAVING</h5>
  <p>Lorem ipsum dolor sit amet consectetuerad</p>
  <div class="more">READ MORE</div>
</div>
<div class="svc-card" style="left:610px">
  <div class="icon-wrap"><span class="backdrop"></span>
  <svg width="50" height="56" viewBox="0 0 50 56"><rect x="20" y="4" width="22" height="24" rx="4" transform="rotate(40 31 16)" fill="none" stroke="var(--red)" stroke-width="2.5"/><path d="M22 30L6 50" stroke="var(--red)" stroke-width="3"/></svg></div>
  <h5>STYLING</h5>
  <p>Lorem ipsum dolor sit amet consectetuerad</p>
  <div class="more">READ MORE</div>
</div>
<div class="svc-card" style="left:835px;padding-top:58px">
  <div class="icon-wrap"><span class="backdrop"></span>
  <svg width="50" height="56" viewBox="0 0 50 56"><rect x="16" y="10" width="16" height="38" rx="6" transform="rotate(30 24 29)" fill="none" stroke="var(--sky)" stroke-width="2.5"/><path d="M28 6h12" stroke="var(--sky)" stroke-width="2.5"/></svg></div>
  <h5>TRIMMING</h5>
  <p>Lorem ipsum dolor sit amet consectetuerad</p>
  <div class="more">READ MORE</div>
</div>

<!-- reviews -->
<section class="band" style="top:2659px;height:523px"></section>
<h2 class="heading section-title" style="top:2726px">Happy customers reviews</h2>
<div class="title-rule" style="top:2788px"></div>
<div class="quote-mark" aria-hidden="true">“</div>
<p class="abs review-text">I love how you treat your customers. You guys are great! Thanks you your amazing staff I have this awesome look that makes everyone jealous. It matters when you give advice and share your opinion. Thanks again, you rock.</p>
<div class="review-name">MARCUS REED</div>
<svg class="abs" style="left:176px;top:3088px" width="44" height="20" viewBox="0 0 44 20"><path d="M10 3L4 10l6 7" fill="none" stroke="#b8c8d6" stroke-width="2"/><path d="M28 3l6 7-6 7" fill="none" stroke="var(--blue)" stroke-width="2"/></svg>
<div class="photo" style="left:600px;top:2830px;width:438px;height:373px;background:radial-gradient(ellipse 35% 30% at 45% 55%,#b08468 0%,#6e4a36 50%,transparent 85%),radial-gradient(ellipse 30% 25% at 70% 80%,#4a2f22 0%,transparent 80%),linear-gradient(150deg,#6a6e70,#3a3c3e 55%,#5d5954)" role="img" aria-label="Barber trimming a customer's beard with a comb"></div>
<svg class="abs" style="left:782px;top:2984px" width="72" height="48" viewBox="0 0 72 48" aria-hidden="true"><rect x="2" y="2" width="68" height="44" rx="14" fill="none" stroke="var(--red)" stroke-width="3"/><path d="M29 14l16 10-16 10z" fill="var(--red)"/></svg>

<!-- stylists -->
<h2 class="heading section-title" style="top:3286px">Our stylist</h2>
<div class="stylist" style="left:160px">
  <div class="shot" role="img" aria-label="Female stylist in a black apron"></div>
  <div class="info"><h6>FREYA LUND</h6><div class="role">Haircutting</div><div class="socials"><span></span><span></span><span></span></div></div>
</div>
<div class="stylist" style="left:463px">
  <div class="shot" role="img" aria-label="Female stylist holding scissors"></div>
  <div class="info"><h6>INGRID HALE</h6><div class="role">Haircutting</div><div class="socials"><span></span><span></span><span></span></div></div>
</div>
<div class="stylist" style="left:766px">
  <div class="shot" role="img" aria-label="Female stylist holding a round brush and hair dryer"></div>
  <div class="info"><h6>ASTRID MOORE</h6><div class="role">Haircutting</div><div class="socials"><span></span><span></span><span></span></div></div>
</div>
<div class="btn" style="left:546px;top:3895px;width:108px;height:37px">View all</div>

<!-- products -->
<h2 class="heading section-title" style="top:4018px">Our products</h2>
<div class="arrow-box" style="left:106px;top:4243px"><svg width="10" height="14" viewBox="0 0 10 14"><path d="M8 1L2 7l6 6" fill="none" stroke="var(--blue)" stroke-width="2"/></svg></div>
<div class="arrow-box" style="left:1061px;top:4243px"><svg width="10" height="14" viewBox="0 0 10 14"><path d="M2 1l6 6-6 6" fill="none" stroke="var(--blue)" stroke-width="2"/></svg></div>
<div class="product" style="left:162px"><div class="pic" role="img" aria-label="Beard shampoo bottle and box" style="background:radial-gradient(ellipse 45% 50% at 50% 55%,#3c6b84 0%,#7fa9b0 55%,rgba(255,255,255,0) 80%)"></div><h6>BEARD SHAMPOO</h6><div class="price">$44.39</div></div>
<div class="product" style="left:340px"><div class="pic" role="img" aria-label="Navy T-shirt with a red graphic" style="background:radial-gradient(circle at 50% 50%,#c62634 0,#c62634 12%,#1f2d55 14%,#2a3a66 55%,rgba(255,255,255,0) 72%)"></div><h6>T SHIRT</h6><div class="price">$35.39</div></div>
<div class="product" style="left:518px"><div class="pic" role="img" aria-label="Shaving brush with black handle" style="background:radial-gradient(ellipse 40% 28% at 50% 28%,#e0dbd2 0%,rgba(255,255,255,0) 100%),radial-gradient(ellipse 22% 35% at 50% 70%,#111 0%,#2a2a2a 60%,rgba(255,255,255,0) 100%)"></div><h6>SHAVE BRUSH</h6><div class="price">$24.39</div></div>
<div class="product" style="left:697px"><div class="pic" role="img" aria-label="Black cap with a red emblem" style="background:radial-gradient(ellipse 50% 35% at 50% 55%,#1a1a1a 0%,#333 60%,rgba(255,255,255,0) 100%)"></div><h6>CAP</h6><div class="price">$14.39</div></div>
<div class="product" style="left:876px"><div class="pic" role="img" aria-label="Beard oil bottle and box" style="background:radial-gradient(ellipse 45% 50% at 50% 55%,#6b4530 0%,#b98d6a 55%,rgba(255,255,255,0) 82%)"></div><h6>BEARD OIL</h6><div class="price">$15.39</div></div>
<div class="btn" style="left:482px;top:4443px;width:112px;height:39px">View all</div>
<div class="btn red" style="left:602px;top:4443px;width:116px;height:39px">Shop now</div>

<!-- map -->
<div class="map" role="img" aria-label="Street map showing the shop location"></div>
<svg class="abs" style="left:592px;top:4724px" width="22" height="30" viewBox="0 0 22 30"><path d="M11 29C4 19 1 15 1 10a10 10 0 0 1 20 0c0 5-3 9-10 19z" fill="var(--red)"/><circle cx="11" cy="10" r="4" fill="#fff"/></svg>
<div class="abs" style="left:672px;top:4700px;width:148px;height:50px;background:var(--red);color:#fff;font-size:12px;line-height:18px;padding:7px 10px">48 Harbor Lane,<br>Suite 2 Brookfield</div>

<!-- contact -->
<section class="contact" role="img" aria-label="Dim barbershop interior"></section>
<p class="centered invite">WE INVITE YOU TO CONTACT US</p>
<p class="centered invite-phone">+1 555 309 7712</p>
<div class="info-col" style="left:226px">
  <h6><svg width="16" height="20" viewBox="0 0 22 30"><path d="M11 29C4 19 1 15 1 10a10 10 0 0 1 20 0c0 5-3 9-10 19z" fill="var(--sky)"/><circle cx="11" cy="10" r="4" fill="#2b2d2f"/></svg>ADDRESS</h6>
  <p>48 Harbor Lane,<br>Suite 2 Brookfield, VERMONT</p>
</div>
<div class="info-col" style="left:530px">
  <h6><svg width="16" height="16" viewBox="0 0 24 24"><path d="M6.6 10.8a15 15 0 0 0 6.6 6.6l2.2-2.2 4.6 1.6V20A17 17 0 0 1 3 4h4l1.6 4.6z" fill="var(--sky)"/></svg>PHONE / E-MAIL</h6>
  <p>+1 555 309 7712<br>info@torbcutters.com</p>
</div>
<div class="info-col" style="left:783px">
  <h6><svg width="16" height="16" viewBox="0 0 24 24"><path d="M2 11l20-9-8 20-3-8z" fill="var(--sky)"/></svg>OPENING HOURS</h6>
  <p>Monday - Friday: 8:00 - 16:00<br>Saturday: 8:00 - 15:00</p>
</div>

<!-- footer -->
<footer class="footer">
  <div class="copy">Copyright © 2021 TORB CUTTERS. All Rights Reserved.</div>
  <div class="soc"><span style="background:#2b5fa8"></span><span style="background:var(--sky)"></span><span style="background:#1f5f95"></span><span style="background:var(--red)"></span></div>
</footer>

</body>
</html>
```